International game business needs app design

We are planning to release a new mobile game on iOS7 which requires a fresh, flat, reduced and functional design, fulfilling Norvex’s iOS7 design guidelines
.
The design shall be created for a dashboard, where players should be able to pick levels (icon + short description; 300+ levels), opponents (icon/photo/avatar image + short description; 5-100) and read/delete system/chat messages (icon, 2-3 actions (delete, accept/decline), text with up to 500 characters; 1-100 entries), Menu bar (settings, shop, leaderboards, achievements, and one or two more menu items) It must consider means to search/select levels and opponents. Would be nice to have an option to start playing immediately (with a random opponent on a random level)

Overall Style/Look: fresh, flat, functional, lot’s of free space, warm color scheme. If full screen images are being used it must be considered that there are user-generated photos or avatars which have to work with it in combination

Ideally the design is responsive and would work both on a smartphone and a tablet. Smartphone is top priority, tablet is optional.

The app will be a game for women predominantly, aged 25-35, with higher education and household net income, which should be reflected in color scheme, icons and navigation.

Some of us like flat design, so you might stick to that or impress all of us with something completely new!

The winner will have the chance to design all screens for the app and will have access to a much bigger budget.

UPDATE: A wireframe is attached - but you don't have to follow the depicted layout. Actually it would be highly appreciated if you could come up with something new. The only important thing is that all the listed components must appear somehow on the dashboard.

Target Market(s)

US, AU, NZ, GB, CA

Industry/Entity Type

Education

Colors

Designer to choose colors to be used in the design.

Requirements
Must have
• All the functional components described above.
Design must be in line with iOS7 design guidelines https://builders.norvexlabs.example/library/ios/documentation/UserExperience/Conceptual/MobileHIG/index.html
Nice to have
• We would like to have someone with the following attributes:
* minimum 5 ios design in your past at least 2 of them responsive – please provide links to the apps you created
* besides UI designer skills would be nice you to have UX skills

The most important factors for us are quality, creativity, speed, flexibility (“be able to take criticism into account”)
Should not have
• We don’t want a girly design so please don’t use too much pinks, flowers and such. The design should be acceptable by men too.

```html
<!DOCTYPE html>
<html lang="en">
<head>
<meta charset="utf-8">
<title>Game Dashboard</title>
<link href="https://fonts.googleapis.com/css2?family=Open+Sans:wght@300;400;600;700&display=swap" rel="stylesheet">
<style>
:root{
  --status:#2e2c40;
  --nav:#45416d;
  --nav-icon:#8f8bb0;
  --accent:#dc4a68;
  --navy:#2f2b5c;
  --page:#f1f1f1;
  --card:#ffffff;
  --bar:#c9c9c9;
  --bar-line:#dcdcdc;
  --ink:#444444;
  --muted:#9a9a9a;
  --ok:#7cbf4a;
  --placeholder:#c7ccd3;
}
*{box-sizing:border-box;margin:0;padding:0}
html,body{width:684px;height:1200px;overflow:hidden;background:var(--page)}
body{font-family:"Open Sans",sans-serif;color:var(--ink);position:relative}
.status-bar{position:absolute;left:0;top:0;width:684px;height:35px;background:var(--status);color:#e6e6e6;font-weight:700;font-size:25px;display:flex;align-items:center;justify-content:space-between;padding:0 12px}
.status-left,.status-right{display:flex;align-items:center;gap:8px}
.nav-bar{position:absolute;left:0;top:35px;width:684px;height:69px;background:var(--nav);display:flex;justify-content:space-around;align-items:center;padding:0 60px}
.nav-bar svg{width:32px;height:32px}
.levels{position:absolute;left:0;top:104px;width:684px;height:140px;background:linear-gradient(180deg,#e9e9e9,#f7f7f7 50%,#ececec)}
.level-track{position:absolute;top:78px;height:8px}
.level{position:absolute;top:52px;width:60px;height:60px;border-radius:50%;border:4px solid #fff;color:#fff;text-align:center;box-shadow:0 1px 3px rgba(0,0,0,.2)}
.level b{display:block;font-size:24px;line-height:28px;margin-top:6px}
.level small{display:block;font-size:9px;line-height:9px}
.level.done{background:var(--accent)}
.level.open{background:var(--navy)}
.search{position:absolute;left:22px;top:265px;width:631px;height:43px;background:#fff;border-radius:6px;color:#9a9a9a;font-size:19px;font-weight:300;display:flex;align-items:center;justify-content:center}
.search svg{position:absolute;right:18px;top:10px}
.opponent{position:absolute;left:8px;width:665px;height:240px;background:var(--card)}
.avatar{position:absolute;left:14px;top:21px;width:153px;height:153px;border-radius:50%;background:var(--placeholder)}
.opponent h2{position:absolute;left:197px;top:18px;font-size:23px;font-weight:600;color:#444}
.opponent p{position:absolute;left:197px;width:428px;font-size:12.5px;line-height:17px;color:var(--muted);font-weight:400}
.opponent .bio{top:66px}
.opponent .note{top:134px}
.actions{position:absolute;left:0;bottom:0;width:665px;height:46px;background:var(--bar);display:flex}
.action{display:flex;align-items:center;justify-content:center;gap:14px;color:#fff;font-size:14px;border-right:2px solid var(--bar-line)}
.action:last-child{border-right:0}
.action:nth-child(1){width:214px}
.action:nth-child(2){width:225px}
.action:nth-child(3){width:226px}
.notice{position:absolute;top:873px;height:218px;background:var(--card);box-shadow:0 0 2px rgba(0,0,0,.12)}
.notice .close{position:absolute;top:7px;right:8px;width:22px;height:22px;background:#b5b5b5;color:#fff;font-size:14px;font-weight:700;text-align:center;line-height:21px}
.message{left:8px;width:324px}
.message .thumb{position:absolute;left:26px;top:34px;width:46px;height:62px;border-radius:20px;background:var(--placeholder)}
.message .from{position:absolute;left:106px;top:14px;font-size:12px;color:var(--accent)}
.message h3{position:absolute;left:106px;top:36px;font-size:17px;font-weight:600}
.message p{position:absolute;left:106px;top:77px;width:182px;font-size:12.5px;line-height:17px;color:var(--muted)}
.invite{left:350px;width:323px}
.invite .art{position:absolute;left:7px;top:5px;width:309px;height:142px;background:var(--placeholder)}
.invite p{position:absolute;left:19px;top:153px;width:178px;font-size:12.5px;line-height:17px;color:var(--muted)}
.invite p span{color:var(--accent)}
.invite .choices{position:absolute;right:14px;top:165px;display:flex;gap:12px}
.play{position:absolute;left:45px;top:1118px;width:582px;height:70px;background:var(--accent);color:#fff;font-size:29px;font-weight:600;display:flex;align-items:center;justify-content:center}
</style>
</head>
<body>
<header class="status-bar">
  <div class="status-left">
    <svg width="46" height="18" viewBox="0 0 46 18"><rect x="0" y="11" width="6" height="7" fill="#e6e6e6"/><rect x="8" y="8" width="6" height="10" fill="#e6e6e6"/><rect x="16" y="5" width="6" height="13" fill="#e6e6e6"/><rect x="24" y="2" width="6" height="16" fill="#e6e6e6"/><rect x="32" y="0" width="6" height="18" fill="#e6e6e6"/></svg>
    <span>DINE</span>
  </div>
  <span>10:35 AM</span>
  <div class="status-right">
    <svg width="22" height="22" viewBox="0 0 22 22"><circle cx="11" cy="11" r="10" fill="#e6e6e6"/><path d="M11 5v6h5" stroke="#2e2c40" stroke-width="2.5" fill="none"/></svg>
    <span>65%</span>
    <svg width="46" height="22" viewBox="0 0 46 22"><rect x="1.5" y="1.5" width="38" height="19" fill="none" stroke="#e6e6e6" stroke-width="3"/><rect x="5" y="5" width="22" height="12" fill="#e6e6e6"/><rect x="41" y="7" width="4" height="8" fill="#e6e6e6"/></svg>
  </div>
</header>

<nav class="nav-bar" aria-label="Main menu">
  <svg viewBox="0 0 32 32" aria-label="Settings"><circle cx="16" cy="16" r="9" fill="none" stroke="var(--nav-icon)" stroke-width="6" stroke-dasharray="4.5 2.6"/><circle cx="16" cy="16" r="6" fill="none" stroke="var(--nav-icon)" stroke-width="3"/></svg>
  <svg viewBox="0 0 32 32" aria-label="Shop"><path d="M2 5h5l4 16h16l3-12H9" fill="none" stroke="var(--nav-icon)" stroke-width="3"/><circle cx="13" cy="27" r="2.5" fill="var(--nav-icon)"/><circle cx="24" cy="27" r="2.5" fill="var(--nav-icon)"/><rect x="17" y="10" width="3" height="6" fill="var(--nav-icon)"/><rect x="17" y="17" width="3" height="2.5" fill="var(--nav-icon)"/></svg>
  <svg viewBox="0 0 32 32" aria-label="Leaderboards"><path d="M7 2h13l6 6v22H7z" fill="none" stroke="var(--nav-icon)" stroke-width="2.5"/><path d="M11 14h11M11 19h11M11 24h11" stroke="var(--nav-icon)" stroke-width="2"/></svg>
  <svg viewBox="0 0 32 32" aria-label="Achievements"><circle cx="16" cy="15" r="6" fill="var(--nav-icon)"/><rect x="13" y="21" width="6" height="5" fill="var(--nav-icon)"/><path d="M16 2v4M5 6l3 3M27 6l-3 3M2 15h4M26 15h4" stroke="var(--nav-icon)" stroke-width="2"/></svg>
</nav>

<section class="levels" aria-label="Levels">
  <div class="level-track" style="left:0;width:293px;background:var(--accent)"></div>
  <div class="level-track" style="left:293px;width:391px;background:var(--navy)"></div>
  <div class="level done" style="left:50px"><b>1</b><small>level</small></div>
  <div class="level done" style="left:157px"><b>2</b><small>level</small></div>
  <div class="level open" style="left:263px"><b>3</b><small>level</small></div>
  <div class="level open" style="left:370px"><b>4</b><small>level</small></div>
  <div class="level open" style="left:474px"><b>5</b><small>level</small></div>
  <div class="level open" style="left:572px"><b>6</b><small>level</small></div>
</section>

<div class="search">search opponent
  <svg width="26" height="26" viewBox="0 0 26 26"><circle cx="10" cy="10" r="8" fill="none" stroke="#b5b5b5" stroke-width="1.5"/><path d="M16 16l8 8" stroke="#b5b5b5" stroke-width="1.5"/></svg>
</div>

<article class="opponent" style="top:347px">
  <div class="avatar" role="img" aria-label="Profile photo of Clara Denton"></div>
  <h2>Clara Denton</h2>
  <p class="bio">Lorem ipsum dolor sit amet, pro propriae nominati consequuntur ut, eos nibh velit et. Noster scripserit et per, odio iuvaret aliquando duo cu, an cum ubique concludaturque.</p>
  <p class="note">Eos impedit signiferumque id, sed ex ipsum civibus explicari, errem</p>
  <div class="actions">
    <div class="action"><svg width="24" height="24" viewBox="0 0 24 24"><path d="M12 1l3.3 7.2 7.7.7-5.8 5.2 1.7 7.7L12 17.8 5.1 21.8l1.7-7.7L1 8.9l7.7-.7z" fill="#fff"/></svg>level 18</div>
    <div class="action"><svg width="26" height="24" viewBox="0 0 26 24"><path d="M13 23S1 15 1 7.5A6 6 0 0 1 13 5a6 6 0 0 1 12 2.5C25 15 13 23 13 23z" fill="#fff"/></svg>add as friend</div>
    <div class="action"><svg width="26" height="24" viewBox="0 0 26 24"><path d="M1 1h24v16H9l-6 6v-6H1z" fill="#fff"/></svg>chat</div>
  </div>
</article>

<article class="opponent" style="top:610px">
  <div class="avatar" role="img" aria-label="Profile photo of Mira x"></div>
  <h2>Mira x</h2>
  <p class="bio">Lorem ipsum dolor sit amet, pro propriae nominati consequuntur ut, eos nibh velit et. Noster scripserit et per, odio iuvaret aliquando duo cu, an cum ubique concludaturque.</p>
  <p class="note">Eos impedit signiferumque id, sed ex ipsum civibus explicari, errem</p>
  <div class="actions">
    <div class="action"><svg width="24" height="24" viewBox="0 0 24 24"><path d="M12 1l3.3 7.2 7.7.7-5.8 5.2 1.7 7.7L12 17.8 5.1 21.8l1.7-7.7L1 8.9l7.7-.7z" fill="#fff"/></svg>level 21</div>
    <div class="action"><svg width="26" height="24" viewBox="0 0 26 24"><path d="M13 23S1 15 1 7.5A6 6 0 0 1 13 5a6 6 0 0 1 12 2.5C25 15 13 23 13 23z" fill="#fff"/></svg>add as friend</div>
    <div class="action"><svg width="26" height="24" viewBox="0 0 26 24"><path d="M1 1h24v16H9l-6 6v-6H1z" fill="#fff"/></svg>chat</div>
  </div>
</article>

<aside class="notice message">
  <div class="close">x</div>
  <div class="thumb" role="img" aria-label="Avatar of Owen Haskell"></div>
  <span class="from">message from</span>
  <h3>Owen Haskell</h3>
  <p>Ex timeam nostrum his, usu eius oportere ea, quod vero nostro at duo. Nam cu mutat eloquentiam, sea et posse ornatus, eam latine labores phaedrum at.</p>
</aside>

<aside class="notice invite">
  <div class="art" role="img" aria-label="Cover artwork of the game Castle Quest Outposts"></div>
  <div class="close">x</div>
  <p>Your friend <span>Leona P</span> just played a game. Wanna try it too?</p>
  <div class="choices">
    <svg width="22" height="22" viewBox="0 0 22 22" aria-label="Accept"><circle cx="11" cy="11" r="11" fill="var(--ok)"/><path d="M6 11l3.5 3.5L16 8" stroke="#fff" stroke-width="2.5" fill="none"/></svg>
    <svg width="22" height="22" viewBox="0 0 22 22" aria-label="Decline"><circle cx="11" cy="11" r="11" fill="var(--accent)"/><path d="M7 7l8 8M15 7l-8 8" stroke="#fff" stroke-width="2.5"/></svg>
  </div>
</aside>

<div class="play">Play a random game</div>
</body>
</html>
```